Stationery Design Project for Nimbora, Chicago

Nimbora, a street parking application which helps car drivers find a street parking spot by offering an ideal path along which to look for parking. This path is calculated by our algorithm based on data (e.g. historical data, baseball games schedule, etc.). Along this path the driver will find a spot and will also save 70% of the search time. Customer we target is reg. between 21 and 45 yo.

We envision something young, fresh, bright and original. Slightly abstract maybe. It should represent the idea and elements of finding street parking in the city, e.g. car(s), parking spot, people, city, etc. (just ideas!).

Logo is attached.

Requirement:
- Business Cards (2 Sided Full Color CMYK)
- Letterhead (1 Sided Full Color CMYK)
- Envelope (1 Sided Full Color CMYK)
- Sticker (1 Sided Full Color CMYK), round with a 2inch diameter.

Reason: We're starting to get more and more designs and need more time to look into all of them. Very exciting!! Thanks to everybody!

Hi all, we're in the process of selecting our favs. Though choices!!! Really good submissions. Will keep you posted and sorry for the delay.

Target Market(s)

Car drivers and owners between 21 and 45

Industry/Entity Type

Parking

Requirements
Must have
• Sticker should be round and include company URL nimbora.com and the new logo which we will attach soon.
Should not have
• Should not be too serious or boring.

```html
<!DOCTYPE html>
<html lang="en">
<head>
<meta charset="utf-8">
<title>Nimbora Business Cards</title>
<link rel="stylesheet" href="https://fonts.googleapis.com/css2?family=Source+Sans+3:wght@400;600;700&display=swap">
<style>
:root{
  --stage:#a77d20;
  --card:#ffffff;
  --ink:#1c1c1c;
  --text:#2a2a2a;
  --accent:#1a8fd6;
  --brand-deep:#2c3ea6;
  --brand-light:#45b8ea;
  --bar-dark:#0c0c0c;
  --bar-mid:#5c5c5c;
}
*{margin:0;padding:0;box-sizing:border-box}
html,body{width:1200px;height:686px;overflow:hidden}
body{background:var(--stage);font-family:"Source Sans 3",sans-serif;color:var(--text);position:relative}
.card{position:absolute;width:510px;height:292px;background:var(--card);border-radius:13px;overflow:hidden;box-shadow:0 2px 5px rgba(0,0,0,.35)}
.card--front-a{left:67px;top:47px}
.card--front-b{left:67px;top:360px}
.card--back{left:645px;top:224px}
.brand{position:absolute;display:flex;align-items:center;gap:14px}
.brand__mark{border-radius:50%;background:var(--brand-deep)}
.brand__name{font-weight:600;color:var(--ink);letter-spacing:.5px}
.card--front-a .brand,.card--front-b .brand{left:106px;top:49px}
.card--front-a .brand__mark,.card--front-b .brand__mark{width:82px;height:82px}
.card--front-a .brand__name,.card--front-b .brand__name{font-size:48px}
.card--back .brand{left:50%;top:136px;transform:translate(-50%,-50%);gap:18px}
.card--back .brand__mark{width:110px;height:110px}
.card--back .brand__name{font-size:54px}
.identity{position:absolute;left:0;width:100%;text-align:center;top:156px}
.identity__name{font-size:16px;font-weight:700;color:var(--accent)}
.identity__title{font-size:12px;font-weight:700;color:var(--ink)}
.identity__address{font-size:12.5px;margin-top:1px}
.contacts{display:flex;justify-content:center;gap:14px;margin-top:4px;font-size:12.5px}
.contact{display:flex;align-items:center;gap:3px}
.icon{width:11px;height:11px;fill:var(--accent)}
.stack{position:absolute;top:159px;right:283px;text-align:right;line-height:1.25}
.stack .identity__name{font-size:16px}
.stack .identity__title{font-size:12.5px;margin-bottom:4px}
.stack .identity__address{font-size:12.5px;line-height:1.3}
.divider{position:absolute;left:244px;top:163px;width:1px;height:62px;background:var(--ink)}
.contact-list{position:absolute;left:263px;top:162px;font-size:12.5px;display:flex;flex-direction:column;gap:7px}
.band{position:absolute;left:0;bottom:0;width:510px;height:30px}
.band__url{position:absolute;right:55px;bottom:6px;font-size:12px;font-weight:700;color:#fff;letter-spacing:1.3px}
</style>
</head>
<body>
<svg width="0" height="0" style="position:absolute">
  <defs>
    <linearGradient id="barGrad" x1="0" x2="1">
      <stop offset="0" stop-color="var(--bar-dark)"/>
      <stop offset=".5" stop-color="var(--bar-mid)"/>
      <stop offset="1" stop-color="var(--bar-dark)"/>
    </linearGradient>
    <linearGradient id="blueGrad" x1="0" x2="1">
      <stop offset="0" stop-color="#2a3a9e"/>
      <stop offset=".75" stop-color="#3aa5e2"/>
      <stop offset="1" stop-color="#2c5fc0"/>
    </linearGradient>
    <symbol id="i-phone" viewBox="0 0 12 12"><path d="M3 1l2 2.5-1.2 1.2c.6 1.3 1.8 2.5 3.1 3.1L8.1 6.6 10.6 8.6 9.4 10.8C5 10.5 1.5 7 1.2 2.6z"/></symbol>
    <symbol id="i-fax" viewBox="0 0 12 12"><path d="M3 1h6v3H3zM1 5h10v4H9v2H3V9H1zM4 8v2h4V8z"/></symbol>
    <symbol id="i-mail" viewBox="0 0 12 12"><path d="M1 3h10v6H1zM1.6 3.4 6 6.6l4.4-3.2v-.1H1.6z"/></symbol>
    <symbol id="band" viewBox="0 0 510 30">
      <path d="M0 12h290l-8 18H0z" fill="url(#barGrad)"/>
      <path d="M288 30l9-18H290z" fill="#fff"/>
      <path d="M290 30l12-30h208v30z" fill="url(#blueGrad)"/>
    </symbol>
  </defs>
</svg>

<section class="card card--front-a">
  <div class="brand"><span class="brand__mark"></span><span class="brand__name">Nimbora</span></div>
  <div class="identity">
    <p><span class="identity__name">Your Name</span><span class="identity__title">, Title</span></p>
    <p class="identity__address">Street name City, State, zip code</p>
    <div class="contacts">
      <span class="contact"><svg class="icon"><use href="#i-phone"/></svg>123-456-7890</span>
      <span class="contact"><svg class="icon"><use href="#i-fax"/></svg>123-456-7890</span>
      <span class="contact"><svg class="icon"><use href="#i-mail"/></svg>name@website.com</span>
    </div>
  </div>
  <svg class="band"><use href="#band"/></svg>
  <span class="band__url">www.website.com</span>
</section>

<section class="card card--front-b">
  <div class="brand"><span class="brand__mark"></span><span class="brand__name">Nimbora</span></div>
  <div class="stack">
    <p class="identity__name">Your Name</p>
    <p class="identity__title">Title</p>
    <p class="identity__address">Street name City<br>State, zip code</p>
  </div>
  <span class="divider"></span>
  <div class="contact-list">
    <span class="contact"><svg class="icon"><use href="#i-phone"/></svg>123-456-7890</span>
    <span class="contact"><svg class="icon"><use href="#i-fax"/></svg>123-456-7890</span>
    <span class="contact"><svg class="icon"><use href="#i-mail"/></svg>name@website.com</span>
  </div>
  <svg class="band"><use href="#band"/></svg>
  <span class="band__url">www.website.com</span>
</section>

<section class="card card--back">
  <div class="brand"><span class="brand__mark"></span><span class="brand__name">Nimbora</span></div>
  <svg class="band"><use href="#band"/></svg>
  <span class="band__url">www.website.com</span>
</section>
</body>
</html>
```